Meridale Accountants needs a stationery design

We need a stationery design for our new innovative accountancy practise - it is to look professional and reliable but also minimalist, crisp, innovative and fresh. Avoid the use of block colour. You must include letterhead.

We look after business clients and help them get started and grow to successful companies. We provide a range of software, accounting, taxation and business consulting services to these clients.

This is a spin off from our more traditional existing practise - we would like to use the same green and blue.

The final design should communicate professional expertise coupled with innovative technology and personal care. The font of the type should reflect this - so far we have received standard font only.

We need business cards, letterhead, with comp slips, We need to see the whole set to form a view, not just the businesscard

I have uploaded the colours that we want to use from our existing letterhead, being the green and blue. We need to use the KTR logo - also enclosed - please use the text from the enclosed letterhead, but don't refer to this for design purposes - this was our temporary draft only.

Target Market(s)

Small to medium companies, high wealth investor clients

Industry/Entity Type

Professional Service

Requirements
Must have
• Crisp, simple design but evoking innovation, technology, competence and difference.
• So far the designs are too standard and not showing innovation.

```html
<!DOCTYPE html>
<html lang="en">
<head>
<meta charset="utf-8">
<title>Meridale Accountants – Stationery Set</title>
<link rel="stylesheet" href="https://fonts.googleapis.com/css2?family=Jost:wght@400;500&family=Source+Sans+3:wght@400;600&display=swap">
<style>
  :root {
    --backdrop: #a9a8aa;
    --paper: #f5f4f2;
    --green: #6f9130;
    --blue: #2f4f8f;
    --navy: #1d3868;
    --card-blue: #30599a;
    --ink: #444;
    --badge: #e8c41a;
  }
  * { margin: 0; padding: 0; box-sizing: border-box; }
  html, body { width: 1200px; height: 770px; overflow: hidden; }
  body { background: var(--backdrop); position: relative; font-family: "Jost", sans-serif; color: var(--ink); }
  .sheet { position: absolute; background: var(--paper); box-shadow: 2px 3px 8px rgba(0,0,0,.25); }
  .brand { position: absolute; font-family: "Jost", sans-serif; font-weight: 400; color: var(--green); white-space: nowrap; line-height: 1; }
  .tagline { position: absolute; font-family: "Jost", sans-serif; color: var(--blue); white-space: nowrap; line-height: 1; }
  .contact { position: absolute; font-family: "Jost", sans-serif; color: #3a3a3a; white-space: nowrap; }
  .contact .firm { color: var(--blue); }
  .icon { display: inline-block; vertical-align: -1px; fill: var(--blue); }

  /* Letterhead */
  .letterhead { left: 62px; top: 33px; width: 496px; height: 701px; }
  .letterhead .brand { left: 36px; top: 66px; font-size: 16px; }
  .letterhead .tagline { left: 36px; top: 85px; font-size: 7.5px; letter-spacing: .3px; }
  .letterhead .contact { left: 332px; top: 40px; font-size: 8.3px; line-height: 10.6px; }
  .letterhead .contact .gap { height: 3px; }
  .letter { position: absolute; left: 35px; top: 196px; width: 427px; font-family: "Source Sans 3", sans-serif; }
  .salutation { font-size: 13px; color: #444; margin-bottom: 26px; }
  .letter p { font-size: 8.2px; line-height: 12px; color: #4a4a4a; margin-bottom: 12px; }
  .signoff { position: absolute; left: 35px; top: 490px; font-family: "Source Sans 3", sans-serif; font-size: 8px; color: #444; }
  .signature { position: absolute; left: 48px; top: 506px; width: 66px; height: 26px; background: linear-gradient(90deg, rgba(40,40,60,.15), rgba(40,40,60,.35), rgba(40,40,60,.1)); border-radius: 40%; }
  .signer { position: absolute; left: 52px; top: 546px; font-family: "Source Sans 3", sans-serif; font-size: 8.5px; line-height: 13px; color: #555; }
  .web-footer { position: absolute; left: 0; right: 0; top: 669px; text-align: center; font-size: 7.5px; letter-spacing: 2.2px; color: #444; }

  /* Business cards */
  .card-front { left: 623px; top: 46px; width: 219px; height: 125px; background: #fbfbfa; }
  .card-front .brand { left: 10px; top: 55px; font-size: 10px; }
  .card-front .tagline { left: 10px; top: 67px; font-size: 4.6px; }
  .card-front .person { position: absolute; left: 115px; top: 14px; font-size: 10px; color: var(--navy); line-height: 1; }
  .card-front .role { position: absolute; left: 115px; top: 25px; font-size: 5.5px; color: var(--green); }
  .card-front .contact { left: 115px; top: 35px; font-size: 5px; line-height: 6.9px; }
  .card-front .contact .gap { height: 3px; }
  .card-back { left: 874px; top: 46px; width: 219px; height: 125px; background: var(--card-blue); }
  .card-back .badge { position: absolute; right: 11px; top: 14px; width: 29px; height: 12px; background: var(--badge); }
  .card-back .brand { left: 0; right: 0; top: 50px; text-align: center; font-size: 13.5px; color: #fff; }
  .card-back .tagline { left: 0; right: 0; top: 68px; text-align: center; font-size: 7px; color: #e4e9f2; }
  .card-back .legal { position: absolute; left: 0; right: 0; top: 98px; text-align: center; font-family: "Source Sans 3", sans-serif; font-size: 5px; line-height: 8px; color: #e4e9f2; }
  .card-back .legal strong { font-weight: 600; color: #fff; }

  /* Compliments slip */
  .comp-slip { left: 587px; top: 194px; width: 560px; height: 254px; }
  .comp-slip .brand { left: 31px; top: 43px; font-size: 17px; }
  .comp-slip .tagline { left: 31px; top: 64px; font-size: 8.5px; letter-spacing: .3px; }
  .comp-title { position: absolute; right: 38px; top: 47px; font-size: 21px; color: var(--navy); }
  .comp-slip .address-line { position: absolute; left: 0; right: 0; top: 207px; text-align: center; font-size: 8.5px; color: #3a3a3a; }
  .comp-slip .rule { position: absolute; left: 29px; right: 38px; top: 222px; border-top: 1px solid #777; }
  .comp-slip .contact-line { position: absolute; left: 0; right: 0; top: 226px; text-align: center; font-size: 8.5px; color: #3a3a3a; }

  /* Envelope */
  .envelope { left: 587px; top: 480px; width: 560px; height: 254px; }
  .envelope .brand { left: 31px; top: 25px; font-size: 17px; }
  .envelope .tagline { left: 31px; top: 46px; font-size: 8.5px; letter-spacing: .3px; }
  .envelope .contact { left: 31px; top: 71px; font-size: 8.3px; line-height: 10.6px; }
  .envelope .contact .gap { height: 3px; }
</style>
</head>
<body>
<svg width="0" height="0" style="position:absolute" aria-hidden="true">
  <symbol id="i-phone" viewBox="0 0 16 16"><path d="M3 1l3 3-1.5 2c1 2 2.5 3.5 4.5 4.5L11 9l3 3-2 3C6 14 2 10 1 3z"/></symbol>
  <symbol id="i-mail" viewBox="0 0 16 16"><rect x="1" y="3" width="14" height="10"/><path d="M1.5 3.5l6.5 5 6.5-5" stroke="#fff" stroke-width="1.2" fill="none"/></symbol>
  <symbol id="i-globe" viewBox="0 0 16 16"><circle cx="8" cy="8" r="7"/><path d="M1 8h14M8 1c-3 3-3 11 0 14M8 1c3 3 3 11 0 14" stroke="#fff" stroke-width="1" fill="none"/></symbol>
  <symbol id="i-mobile" viewBox="0 0 16 16"><rect x="4" y="1" width="8" height="14" rx="1"/><rect x="5.5" y="3" width="5" height="8" fill="#fff"/></symbol>
</svg>

<section class="sheet letterhead">
  <div class="brand">Meridale Accountants</div>
  <div class="tagline">Grow with Clarity</div>
  <div class="contact">
    <div class="firm">Meridale Accountants</div>
    <div>ABN 42 500 318 906</div>
    <div class="gap"></div>
    <div>P O Box 2280, Glenbrook NSW 2773</div>
    <div>Suite 4B, Level 3, 18 Harwood Street</div>
    <div>Glenbrook NSW 2773</div>
    <div class="gap"></div>
    <div><svg class="icon" width="8" height="8"><use href="#i-phone"/></svg> (02) 55501472</div>
    <div><svg class="icon" width="8" height="8"><use href="#i-mail"/></svg> clients@meridaleaccountants.com.au</div>
  </div>
  <div class="letter">
    <div class="salutation">Dear Mr. Hart,</div>
    <p>Lorem ipsum dolor sit amet, consectetur adipiscing elit. Donec orci purus, luctus vitae dignissim eu, iaculis sed purus. Vivamus faucibus, ipsum nec aliquet viverra, leo mauris condimentum ligula, sit amet sagittis enim ligula quis arcu. Nam egestas tortor id nisi porttitor mattis. In tortor ante, ultricies in suscipit a, tempus non massa. Vivamus et auctor mi. Fusce vel massa nulla. Phasellus nec eros mauris, et scelerisque orci.</p>
    <p>Donec malesuada orci vitae nulla accumsan porta a id massa. Quisque accumsan iaculis magna sit amet fringilla. Maecenas consequat, magna eget tincidunt semper, odio nibh rutrum mi, id feugiat ante nisi eu risus. Vestibulum nunc orci, rhoncus a placerat in, ultricies in mi. Cras mattis varius eros, vel fringilla nisi suscipit eget. Quisque scelerisque sagittis nulla at porttitor.</p>
    <p>Sed id augue vitae urna euismod commodo aliquet a quam. Pellentesque arcu velit, cursus et malesuada ut, consequat et diam. Nullam erat sem, rhoncus id ullamcorper vitae, rhoncus et arcu. In ultricies ultricies nulla, ut rutrum nisi iaculis at. Donec eu magna a metus ornare faucibus. Fusce aliquet faucibus ultricies. Morbi semper, est id tincidunt gravida, sem arcu adipiscing lacus, ac bibendum nulla leo eu purus. Quisque nec diam sed risus consectetur a cumsan quis quis nibh. Vestibulum id purus lorem.</p>
    <p>It is a long established fact that a reader will be distracted by the readable content of a page when looking at its layout. The point of using Lorem Ipsum is that it has a more-or-less normal distribution of letters, as opposed to using 'Content here, content here', making it look like readable English. Many desktop publishing packages</p>
  </div>
  <div class="signoff">Sincerely,</div>
  <div class="signature" role="img" aria-label="Handwritten signature"></div>
  <div class="signer">Daniel Hart<br>CEO/ Founder</div>
  <div class="web-footer">www.meridaleaccountants.com.au</div>
</section>

<section class="sheet card-front">
  <div class="brand">Meridale Accountants</div>
  <div class="tagline">Grow with Clarity</div>
  <div class="person">Daniel Hart</div>
  <div class="role">Accountants</div>
  <div class="contact">
    <div class="firm">Meridale Accountants</div>
    <div>ABN 42 500 318 906</div>
    <div>P O Box 2280, Glenbrook NSW 2773</div>
    <div>Suite 4B, Level 3, 18 Harwood Street</div>
    <div>Glenbrook NSW 2773</div>
    <div class="gap"></div>
    <div><svg class="icon" width="5" height="5"><use href="#i-phone"/></svg> (02) 55501472</div>
    <div><svg class="icon" width="5" height="5"><use href="#i-mobile"/></svg> 0400 555 218</div>
    <div><svg class="icon" width="5" height="5"><use href="#i-mail"/></svg> clients@meridaleaccountants.com.au</div>
    <div><svg class="icon" width="5" height="5"><use href="#i-globe"/></svg> www.meridaleaccountants.com.au</div>
  </div>
</section>

<section class="sheet card-back">
  <div class="badge" role="img" aria-label="Professional body badge"></div>
  <div class="brand">Meridale Accountants</div>
  <div class="tagline">Grow with Clarity</div>
  <div class="legal">Liability limited by a Scheme approved under Professional Standards Legislation<br><strong>Meridale Accountants is a KTR Practise</strong></div>
</section>

<section class="sheet comp-slip">
  <div class="brand">Meridale Accountants</div>
  <div class="tagline">Grow with Clarity</div>
  <div class="comp-title">With Compliments</div>
  <div class="address-line"><span style="color:var(--blue)">Meridale Accountants</span>, P O Box 2280, Glenbrook NSW 2773 &nbsp;|&nbsp; Suite 4B, Level 3, 18 Harwood Street, Glenbrook NSW 2773</div>
  <div class="rule"></div>
  <div class="contact-line"><svg class="icon" width="8" height="8"><use href="#i-phone"/></svg> (02) 55501472 &nbsp;| <svg class="icon" width="9" height="8"><use href="#i-mail"/></svg> clients@meridaleaccountants.com.au &nbsp;| <svg class="icon" width="8" height="8"><use href="#i-globe"/></svg> www.meridaleaccountants.com.au &nbsp;| &nbsp;ABN 42 500 318 906</div>
</section>

<section class="sheet envelope">
  <div class="brand">Meridale Accountants</div>
  <div class="tagline">Grow with Clarity</div>
  <div class="contact">
    <div class="firm">Meridale Accountants</div>
    <div>ABN 42 500 318 906</div>
    <div class="gap"></div>
    <div>P O Box 2280, Glenbrook NSW 2773</div>
    <div>Suite 4B, Level 3, 18 Harwood Street</div>
    <div>Glenbrook NSW 2773</div>
  </div>
</section>
</body>
</html>
```